Health Care Company with Logo Needs Business Cards designed

We are a luxury behavioral health company looking for business cards design we already have a logo and are looking for someone to design a sophisticated luxurious looking business card. Please note that Card design should be captivating just like the logo and also encompass the logo color

Industry/Entity Type

Healthcare

Contact Information for Business Card

Logo,company name, tagline, my name and title, contact details, and physical address

```html
<!DOCTYPE html>
<html lang="en">
<head>
<meta charset="utf-8">
<title>Lumera Wellness Group – Business Cards</title>
<link href="https://fonts.googleapis.com/css2?family=Arimo:wght@400;700&display=swap" rel="stylesheet">
<style>
  :root {
    --purple: #763a93;
    --blue: #1aa3e0;
    --ink: #3a3a3a;
    --grey: #555555;
    --line: #4a4a4a;
    --paper: #ffffff;
    --backdrop: #e6e6e4;
  }
  * { margin: 0; padding: 0; box-sizing: border-box; }
  html, body {
    width: 1200px; height: 802px; overflow: hidden;
    background: var(--backdrop);
    font-family: "Arimo", Arial, sans-serif;
  }
  .sheet {
    position: relative; width: 1200px; height: 802px;
    display: flex; align-items: center; justify-content: center; gap: 40px;
  }
  .card {
    position: relative; width: 540px; height: 309px;
    background: var(--paper);
    box-shadow: 0 6px 18px rgba(0,0,0,0.12);
    overflow: hidden;
  }

  /* Brand lockup */
  .brand { position: absolute; display: flex; align-items: center; gap: 10px; }
  .brand-mark { width: 26px; height: 26px; background: var(--purple); flex: none; }
  .brand-name { font-weight: 700; color: var(--purple); font-size: 24px; letter-spacing: -0.3px; line-height: 1; white-space: nowrap; }
  .brand-tagline {
    font-size: 8.5px; font-weight: 700; color: var(--blue);
    letter-spacing: 1.6px; text-transform: uppercase; margin-top: 4px; white-space: nowrap;
  }

  /* Front */
  .front .brand { left: 34px; top: 34px; }
  .holder { position: absolute; left: 34px; top: 112px; }
  .holder-name { color: var(--blue); font-weight: 700; font-size: 22px; }
  .holder-title { color: var(--grey); font-size: 14px; margin-top: 4px; }
  .contact-band {
    position: absolute; left: 0; top: 178px; width: 470px; height: 112px;
    background: var(--purple);
    clip-path: polygon(0 0, 100% 0, 88% 100%, 0 100%);
    padding: 14px 0 0 34px;
  }
  .contact-list { list-style: none; color: #fff; font-size: 14px; line-height: 21px; }
  .contact-list li { display: flex; align-items: center; gap: 10px; white-space: nowrap; }
  .contact-list svg { width: 12px; height: 12px; flex: none; }
  .contact-list .no-icon { padding-left: 22px; }

  /* Back */
  .back .brand { right: 28px; top: 28px; }
  .back .brand-name { font-size: 19px; }
  .back .brand-mark { width: 22px; height: 22px; }
  .back .brand-tagline { font-size: 7px; letter-spacing: 1.2px; }
  .appt-title {
    position: absolute; left: 34px; top: 90px;
    color: var(--blue); font-weight: 700; font-size: 22px; letter-spacing: 0.5px;
  }
  .form { position: absolute; left: 34px; right: 34px; top: 128px; color: var(--ink); font-size: 14px; }
  .row { display: flex; align-items: flex-end; gap: 8px; margin-bottom: 12px; }
  .rule { flex: 1; border-bottom: 1px solid var(--line); height: 16px; }
  .days { display: flex; gap: 14px; flex-wrap: wrap; margin: 4px 0 6px; }
  .check { display: flex; align-items: center; gap: 6px; }
  .box { width: 13px; height: 13px; border: 2px solid var(--blue); }
  .blank-line { border-bottom: 1px solid var(--line); height: 26px; }
</style>
</head>
<body>
<main class="sheet">

  <section class="card front" aria-label="Business card front">
    <div class="brand">
      <span class="brand-mark"></span>
      <div>
        <div class="brand-name">Lumera Wellness Group</div>
        <div class="brand-tagline">Committed to calm, care and renewal</div>
      </div>
    </div>
    <div class="holder">
      <div class="holder-name">Daniel Reyes</div>
      <div class="holder-title">Manager</div>
    </div>
    <div class="contact-band">
      <ul class="contact-list">
        <li><svg viewBox="0 0 12 12"><path d="M2.5 1 L4.5 1 L5 3.5 L3.8 4.5 Q5 7 7.5 8.2 L8.5 7 L11 7.5 L11 9.5 Q11 11 9.5 11 Q1 10 1 2.5 Q1 1 2.5 1Z" fill="#fff"/></svg>555-014-3827</li>
        <li><svg viewBox="0 0 12 12"><rect x="1" y="2.5" width="10" height="7" fill="none" stroke="#fff" stroke-width="1.2"/><path d="M1 2.5 L6 7 L11 2.5" fill="none" stroke="#fff" stroke-width="1.2"/></svg>hello@lumerawellness.example</li>
        <li><svg viewBox="0 0 12 12"><circle cx="6" cy="6" r="5" fill="none" stroke="#fff" stroke-width="1.2"/><path d="M1 6 H11 M6 1 Q3 6 6 11 M6 1 Q9 6 6 11" fill="none" stroke="#fff" stroke-width="1"/></svg>www.lumerawellness.example</li>
        <li class="no-icon">Your address, city, state, ZIP 0000</li>
      </ul>
    </div>
  </section>

  <section class="card back" aria-label="Appointment card back">
    <div class="brand">
      <span class="brand-mark"></span>
      <div>
        <div class="brand-name">Lumera Wellness Group</div>
        <div class="brand-tagline">Committed to calm, care and renewal</div>
      </div>
    </div>
    <h2 class="appt-title">APPOINTMENT</h2>
    <div class="form">
      <div class="row"><span>NAME</span><span class="rule"></span></div>
      <div class="row"><span>DATE</span><span class="rule"></span><span>TIME</span><span class="rule"></span>
        <span class="check"><span class="box"></span>AM</span><span class="check"><span class="box"></span>PM</span></div>
      <div class="days">
        <span class="check"><span class="box"></span>MON</span>
        <span class="check"><span class="box"></span>TUE</span>
        <span class="check"><span class="box"></span>WED</span>
        <span class="check"><span class="box"></span>THU</span>
        <span class="check"><span class="box"></span>FRI</span>
        <span class="check"><span class="box"></span>SAT</span>
      </div>
      <div class="blank-line"></div>
      <div class="blank-line"></div>
    </div>
  </section>

</main>
</body>
</html>
```